IT Company requires new Business Card design.

Over the years we have had a few different business card designs. We are now due for new cards across the board for all staff. We felt this would be a good time to start fresh with a new design. Our traditional card simply had our details on the front, and a list of services on the back. We don't particularly need the list of services, we have had cards where the only thing on the rear of the card was our logo.
Feel free to be creative, we would like our tag line "Complete IT Management" to appear at some point, doesn't necessarily have to be with the logo.
I have attached samples and drafts of various previous cards we have used over the years.

```html
<!DOCTYPE html>
<html lang="en">
<head>
<meta charset="utf-8">
<title>Ridgeline Systems – Business Card</title>
<link href="https://fonts.googleapis.com/css2?family=Open+Sans:wght@400;600;700;800&display=swap" rel="stylesheet">
<style>
  :root {
    --backdrop: #e6e6e4;
    --card: #ffffff;
    --brand: #5e6d78;
    --ink: #4a4f54;
    --ink-soft: #5a5f64;
    --rule: #8a9197;
  }
  * { box-sizing: border-box; margin: 0; padding: 0; }
  html, body {
    width: 1034px; height: 1200px; overflow: hidden;
    background: var(--backdrop);
    font-family: "Open Sans", Arial, sans-serif;
  }
  .card {
    position: absolute; left: 74px; width: 898px; height: 514px;
    background: var(--card);
    box-shadow: 0 2px 6px rgba(0,0,0,0.18);
  }
  .card--front { top: 65px; }
  .card--back { top: 631px; }

  .brand { position: absolute; left: 56px; top: 46px; display: flex; align-items: center; gap: 26px; }
  .brand__square { width: 112px; height: 112px; background: var(--brand); }
  .brand__name {
    color: var(--brand); font-weight: 800; font-size: 52px; line-height: 0.98;
    letter-spacing: 0.5px; text-transform: uppercase;
  }
  .tagline {
    position: absolute; left: 195px; top: 172px;
    color: var(--brand); font-size: 15px; font-weight: 600; letter-spacing: 3.6px;
    text-transform: uppercase;
  }

  .person { position: absolute; left: 57px; top: 286px; }
  .person__name { color: var(--brand); font-weight: 700; font-size: 27px; line-height: 1.2; }
  .person__role { color: var(--ink-soft); font-size: 21px; margin-top: 4px; }
  .website { position: absolute; left: 57px; top: 448px; color: var(--ink); font-size: 22px; }
  .website strong { color: var(--brand); font-weight: 600; }

  .divider { position: absolute; left: 449px; top: 290px; width: 2px; height: 212px; background: var(--rule); }

  .contact { position: absolute; left: 469px; top: 282px; list-style: none; }
  .contact li { display: flex; align-items: center; height: 36px; color: var(--ink); font-size: 21px; }
  .contact svg { width: 20px; height: 20px; margin-right: 12px; fill: var(--brand); flex: none; }
  .address { position: absolute; left: 469px; top: 438px; color: var(--ink); font-size: 21px; line-height: 1.5; }

  .back-brand {
    position: absolute; left: 0; right: 0; top: 140px;
    display: flex; align-items: center; justify-content: center; gap: 30px;
  }
  .back-brand__square { width: 150px; height: 150px; background: var(--brand); }
  .back-brand__name {
    color: var(--brand); font-weight: 800; font-size: 68px; line-height: 1; text-transform: uppercase;
  }
  .back-website {
    position: absolute; left: 0; right: 0; top: 462px; text-align: center;
    color: var(--ink); font-size: 26px; letter-spacing: 3px;
  }
  .back-website strong { color: var(--brand); font-weight: 600; }
</style>
</head>
<body>

<section class="card card--front">
  <div class="brand">
    <div class="brand__square"></div>
    <div class="brand__name">Ridgeline<br>Systems</div>
  </div>
  <p class="tagline">Complete IT Management</p>

  <div class="person">
    <p class="person__name">Marcus Hale</p>
    <p class="person__role">Operation Manager</p>
  </div>
  <p class="website">www.<strong>ridgelinesystems</strong>.com.au</p>

  <div class="divider"></div>

  <ul class="contact">
    <li>
      <svg viewBox="0 0 20 20" aria-hidden="true"><circle cx="10" cy="10" r="9" fill="none" stroke="#5e6d78" stroke-width="1.6"/><path d="M7 5.5c.6-.4 1.2-.2 1.5.4l.8 1.6c.2.5 0 1-.4 1.3l-.5.4c.5 1.2 1.3 2 2.4 2.6l.5-.4c.4-.3 1-.3 1.3.1l1.1 1.2c.4.5.3 1.1-.2 1.5-1 .8-2.6.6-4.2-.6C7.4 12 6 9.4 6.2 7.3c.1-.8.4-1.4.8-1.8z"/></svg>
      08 5550 1846
    </li>
    <li>
      <svg viewBox="0 0 20 20" aria-hidden="true"><rect x="5" y="1" width="10" height="18" rx="2"/><rect x="7" y="3.5" width="6" height="6" fill="#fff"/><rect x="7" y="11.5" width="6" height="5" fill="#fff" opacity=".5"/></svg>
      0400 555 719
    </li>
    <li>
      <svg viewBox="0 0 20 20" aria-hidden="true"><rect x="6" y="2" width="8" height="6" fill="none" stroke="#5e6d78" stroke-width="1.6"/><rect x="2" y="8" width="16" height="9" rx="1.5"/><rect x="5" y="11" width="10" height="2" fill="#fff"/></svg>
      08 5550 1846
    </li>
    <li>
      <svg viewBox="0 0 20 20" aria-hidden="true"><path d="M2 8l8-5 8 5v9H2z"/><path d="M3 8.5l7 4.5 7-4.5" fill="none" stroke="#fff" stroke-width="1.4"/></svg>
      marcus@ridgelinesystems.com.au
    </li>
  </ul>

  <p class="address">Unit 7 22 Harwell Road<br>Kelmscott WA 6111</p>
</section>

<section class="card card--back">
  <div class="back-brand">
    <div class="back-brand__square"></div>
    <div class="back-brand__name">Ridgeline<br>Systems</div>
  </div>
  <p class="back-website">www.<strong>ridgelinesystems</strong>.com.au</p>
</section>

</body>
</html>
```